BOLD & MINIMALIST DESIGN NEEDED

We want a very bold but minimalistic business card design that is impactful and utilizes both sides of the business card. Our current logo is included for your use.

We want bold fonts and good use of negative space. We don't want the logo to overpower the design.

Target Market(s)

Professionals who are building new commercial buildings.

Industry/Entity Type

Construction

Contact Information for Business Card

Name, Title, email, office phone, cell phone, website

Font styles to use
Serif
Sans Serif

Requirements
Must have
• Bold design!

```html
<!DOCTYPE html>
<html lang="en">
<head>
<meta charset="utf-8">
<title>Northridge Business Card</title>
<link rel="stylesheet" href="https://fonts.googleapis.com/css2?family=Poppins:wght@400;700&display=swap">
<style>
  :root {
    --page-bg: #232227;
    --card-bg: #25282a;
    --brand-green: #7ac143;
    --text-white: #ffffff;
    --text-soft: #e6e6e6;
  }
  * { box-sizing: border-box; margin: 0; padding: 0; }
  html, body {
    width: 1200px; height: 801px; overflow: hidden;
    background: var(--page-bg);
    font-family: "Poppins", sans-serif;
  }
  .canvas {
    width: 1200px; height: 801px;
    display: flex; align-items: center; justify-content: center; gap: 48px;
  }
  .card {
    position: relative;
    width: 540px; height: 309px;
    background: var(--card-bg);
    box-shadow: 0 18px 40px rgba(0,0,0,.45);
  }
  .brand-name {
    font-weight: 700;
    color: var(--text-white);
    text-transform: uppercase;
    letter-spacing: 1px;
    display: flex; align-items: center; gap: 10px;
  }
  .brand-dot {
    width: 14px; height: 14px; border-radius: 50%;
    background: var(--brand-green);
  }
  .card-front { display: flex; align-items: center; justify-content: center; }
  .card-front .brand-name { font-size: 38px; }

  .card-back .brand-name {
    position: absolute; left: 40px; bottom: 66px; font-size: 26px;
  }
  .divider {
    position: absolute; left: 292px; top: 70px;
    width: 2px; height: 170px;
    background: var(--brand-green);
  }
  .contact {
    position: absolute; left: 316px; top: 70px;
    color: var(--text-soft);
    font-size: 12px; line-height: 1.5;
  }
  .contact-name {
    color: var(--brand-green); font-weight: 700; font-size: 20px;
    line-height: 1.1; text-transform: uppercase;
  }
  .contact-title { font-size: 12px; margin-bottom: 18px; }
  .contact-address { margin-bottom: 6px; }
  .contact-row { display: flex; align-items: center; gap: 7px; }
  .contact-row svg { width: 11px; height: 11px; flex: none; }
</style>
</head>
<body>
<main class="canvas">
  <section class="card card-front">
    <div class="brand-name"><span class="brand-dot"></span>Northridge</div>
  </section>

  <section class="card card-back">
    <div class="brand-name"><span class="brand-dot"></span>Northridge</div>
    <div class="divider"></div>
    <div class="contact">
      <p class="contact-name">Owen Hale</p>
      <p class="contact-title">Craftsman</p>
      <p class="contact-address">PO BOX 48 Kestrel Lane<br>5th street Geelong</p>
      <p class="contact-row">
        <svg viewBox="0 0 24 24" aria-hidden="true"><path fill="#7ac143" d="M6.6 10.8a15.1 15.1 0 0 0 6.6 6.6l2.2-2.2a1 1 0 0 1 1-.25 11.4 11.4 0 0 0 3.6.57 1 1 0 0 1 1 1V20a1 1 0 0 1-1 1A17 17 0 0 1 3 4a1 1 0 0 1 1-1h3.5a1 1 0 0 1 1 1c0 1.25.2 2.45.57 3.57a1 1 0 0 1-.25 1z"/></svg>
        (555) 210-4471
      </p>
      <p class="contact-row">
        <svg viewBox="0 0 24 24" aria-hidden="true"><rect x="2" y="5" width="20" height="14" fill="#7ac143"/><path d="M2 5l10 8 10-8" fill="none" stroke="#25282a" stroke-width="2"/></svg>
        hello@northridgebuild.com
      </p>
    </div>
  </section>
</main>
</body>
</html>
```